Agriculture Business Card

I want to use my existing logo and use my tagline of "Don't Guess...Soil Test" on the card. Looking for a double sided card that will really get peoples attention.
Contact Info:
Marlow Field Crop Edge
Calvin Brusk
2917 K Lane
Larkin, NE 68593
402-555-0193
calvin.r.brusk@fieldmailbox.net

```html
<!DOCTYPE html>
<html lang="en">
<head>
<meta charset="utf-8">
<title>Marlow Field Crop Edge – Business Card</title>
<link href="https://fonts.googleapis.com/css2?family=Oswald:wght@500;600&family=Arimo:wght@400;700&display=swap" rel="stylesheet">
<style>
  :root{
    --backdrop:#232323;
    --soil:#a05e3b;
    --soil-dark:#94532f;
    --paper:#f7f7f5;
    --corn:#f5b71b;
    --leaf:#3cb22b;
    --leaf-light:#72c24a;
    --ink-light:#ffffff;
  }
  *{margin:0;padding:0;box-sizing:border-box}
  html,body{width:1200px;height:874px;overflow:hidden;background:var(--backdrop)}
  .canvas{position:relative;width:1200px;height:874px}
  .card{position:absolute;width:620px;height:354px;border-radius:22px;overflow:hidden;box-shadow:0 18px 40px rgba(0,0,0,.55)}

  /* back side */
  .card--back{left:330px;top:52px;background:var(--soil-dark)}
  .back-mark{position:absolute;left:0;right:0;top:118px;display:flex;align-items:center;justify-content:center;gap:14px}
  .back-mark__dot{width:34px;height:34px;border-radius:50%;background:var(--leaf)}
  .back-mark__name{font-family:"Oswald",sans-serif;font-weight:600;font-size:40px;color:var(--corn);letter-spacing:.5px}
  .tagline{position:absolute;left:0;right:0;bottom:62px;text-align:center;font-family:"Arimo",sans-serif;font-weight:700;font-size:27px;letter-spacing:.5px}
  .tagline__guess{color:var(--leaf)}
  .tagline__test{color:var(--corn)}

  /* front side */
  .card--front{left:250px;top:470px;background:var(--paper)}
  .front-wave{position:absolute;inset:0}
  .front-mark{position:absolute;left:34px;top:44px;display:flex;align-items:center;gap:12px}
  .front-mark__dot{width:28px;height:28px;border-radius:50%;background:var(--corn)}
  .front-mark__name{font-family:"Oswald",sans-serif;font-weight:500;font-size:30px;line-height:1.05;color:var(--soil);width:180px}
  .holder{position:absolute;right:40px;top:196px;text-align:right}
  .holder__name{font-family:"Oswald",sans-serif;font-weight:600;font-size:32px;color:var(--corn);letter-spacing:.5px;line-height:1}
  .holder__rule{display:block;width:56px;height:2px;background:var(--ink-light);margin:8px 0 8px auto}
  .contact{list-style:none;font-family:"Arimo",sans-serif;font-size:13px;color:var(--ink-light);line-height:1.3}
  .contact li{display:flex;justify-content:flex-end;align-items:center;gap:8px}
  .contact svg{width:11px;height:11px;flex:none}
  .contact .no-icon{margin-right:19px}
</style>
</head>
<body>
<main class="canvas">

  <section class="card card--back" aria-label="Card back">
    <div class="back-mark">
      <span class="back-mark__dot"></span>
      <span class="back-mark__name">Marlow Field Crop Edge</span>
    </div>
    <p class="tagline"><span class="tagline__guess">DON'T GUESS...</span><span class="tagline__test">SOIL TEST</span></p>
  </section>

  <section class="card card--front" aria-label="Card front">
    <svg class="front-wave" viewBox="0 0 620 354" preserveAspectRatio="none" aria-hidden="true">
      <path d="M0,180 C110,290 220,285 330,235 S530,110 620,175 L620,354 L0,354 Z" fill="var(--leaf-light)" transform="translate(0,-14)"/>
      <path d="M0,180 C110,290 220,285 330,235 S530,110 620,175 L620,354 L0,354 Z" fill="var(--leaf)" transform="translate(0,-8)"/>
      <path d="M0,180 C110,290 220,285 330,235 S530,110 620,175 L620,354 L0,354 Z" fill="var(--corn)" transform="translate(0,-2)"/>
      <path d="M0,180 C110,290 220,285 330,235 S530,110 620,175 L620,354 L0,354 Z" fill="var(--soil)" transform="translate(0,5)"/>
    </svg>

    <div class="front-mark">
      <span class="front-mark__dot"></span>
      <span class="front-mark__name">Marlow Field Crop Edge</span>
    </div>

    <div class="holder">
      <h1 class="holder__name">CALVIN BRUSK</h1>
      <span class="holder__rule"></span>
      <ul class="contact">
        <li><span class="no-icon">2917 K Lane</span></li>
        <li>Larkin, NE 68593
          <svg viewBox="0 0 12 12"><path d="M6 0.5a4 4 0 0 1 4 4c0 3-4 7-4 7s-4-4-4-7a4 4 0 0 1 4-4z" fill="var(--corn)"/><circle cx="6" cy="4.5" r="1.5" fill="var(--soil)"/></svg></li>
        <li>402-555-0193
          <svg viewBox="0 0 12 12"><path d="M2.5 1l2 0 1 3-1.5 1a6 6 0 0 0 3 3l1-1.5 3 1v2a1 1 0 0 1-1 1A9.5 9.5 0 0 1 1.5 2a1 1 0 0 1 1-1z" fill="var(--corn)"/></svg></li>
        <li>calvin.r.brusk@fieldmailbox.net
          <svg viewBox="0 0 12 12"><rect x="0.5" y="2.5" width="11" height="7" fill="var(--corn)"/><path d="M0.5 2.5l5.5 4 5.5-4" fill="none" stroke="var(--soil)" stroke-width="1"/></svg></li>
        <li>marlowfieldedge.com
          <svg viewBox="0 0 12 12"><circle cx="6" cy="6" r="5.5" fill="var(--corn)"/><path d="M0.5 6h11M6 0.5c-2.5 3-2.5 8 0 11M6 0.5c2.5 3 2.5 8 0 11" fill="none" stroke="var(--soil)" stroke-width="0.8"/></svg></li>
      </ul>
    </div>
  </section>

</main>
</body>
</html>
```